Blue Heron Journeys

We are a predominantly online travel agency with high-end (first/business class) clients. I'm looking to either have our existing logo revamped or a new logo created with business card layout. I prefer to work with existing logo if possible so it remains familiar with existing clientele. I have uploaded a yellow business card layout showing icons on one side of the card. I would like to keep my existing colours, not yellow. could the company name/tag line go over the icons?
Industry/Entity Type
Business
Contact Information for Business Card
Lucinda Fairley
Director
(I.A.T.A. 07715463)
(Corvano Pty. Ltd) ABN 61 574 203 918
512/18 Kendrick Lane
Wattle Reach | NSW 2577 | Australia
www.blueheronjourneys.com.au
m: + 61 (0) 417 588 130
t: + 61 (0) 2 9416 2058
e: lucinda@blueheronjourneys.com.au

```html
<!DOCTYPE html>
<html lang="en">
<head>
<meta charset="utf-8">
<title>Blue Heron Journeys – Business Card Concept 1.03</title>
<link href="https://fonts.googleapis.com/css2?family=Open+Sans:wght@700&family=Montserrat:wght@400;500;600&family=Playfair+Display:wght@700&display=swap" rel="stylesheet">
<style>
  :root {
    --page: #ffffff;
    --ink: #111111;
    --card-white: #ffffff;
    --card-dark: #404040;
    --band-grey: #6e6e6e;
    --name-grey: #6b6b6b;
    --text-dark: #333333;
    --icon-grey: #666666;
    --frame: #1a1a1a;
  }
  * { box-sizing: border-box; margin: 0; padding: 0; }
  html, body { width: 846px; height: 1200px; overflow: hidden; background: var(--page); }
  .sheet { position: relative; width: 846px; height: 1200px; }

  .concept-title {
    position: absolute; top: 36px; left: 0; width: 846px;
    text-align: center;
    font: 700 45px/1 "Open Sans", sans-serif;
    color: var(--ink);
  }

  .card {
    position: absolute; width: 750px; height: 486px;
    border: 1px solid var(--frame);
    box-shadow: 2px 4px 6px rgba(0,0,0,0.35);
    overflow: hidden;
  }
  .card--front { left: 62px; top: 171px; background: var(--card-white); }
  .card--back { left: 60px; top: 698px; background: var(--card-dark); }

  .card__waves { position: absolute; inset: 0; width: 750px; height: 486px; }

  .holder { position: absolute; left: 47px; top: 70px; }
  .holder__name {
    font: 600 40px/1 "Montserrat", sans-serif;
    color: var(--name-grey);
    letter-spacing: -1px;
  }
  .holder__position {
    margin-top: 4px;
    font: 400 19px/1 "Montserrat", sans-serif;
    color: var(--text-dark);
    letter-spacing: 5.4px;
  }

  .brand {
    position: absolute;
    font-family: "Playfair Display", serif;
    font-weight: 700;
    white-space: nowrap;
  }
  .brand--front { right: 46px; top: 110px; font-size: 26px; color: #555555; }
  .brand--back { left: 0; width: 750px; top: 262px; text-align: center; font-size: 50px; color: #ffffff; }

  .contacts { position: absolute; left: 0; top: 0; list-style: none; }
  .contacts__item { position: absolute; left: 0; display: flex; align-items: flex-start; white-space: nowrap; }
  .contacts__icon { position: absolute; left: 58px; width: 20px; height: 20px; fill: var(--icon-grey); }
  .contacts__text {
    position: absolute; left: 109px;
    font: 500 16.5px/23px "Montserrat", sans-serif;
    color: var(--text-dark);
  }
</style>
</head>
<body>
<main class="sheet">
  <h1 class="concept-title">CONCEPT 1.03</h1>

  <section class="card card--front" aria-label="Business card front">
    <svg class="card__waves" viewBox="0 0 750 486" aria-hidden="true">
      <path d="M0,411 C160,478 420,420 750,301 L750,318 C430,440 170,495 0,428 Z" fill="var(--band-grey)"/>
      <path d="M0,440 C170,505 430,462 750,336 L750,486 L0,486 Z" fill="var(--card-dark)"/>
    </svg>

    <div class="holder">
      <p class="holder__name">YOUR NAME</p>
      <p class="holder__position">YOUR POSITION</p>
    </div>

    <p class="brand brand--front">Blue Heron Journeys</p>

    <ul class="contacts">
      <li class="contacts__item" style="top:224px">
        <svg class="contacts__icon" viewBox="0 0 24 24" aria-hidden="true"><path d="M6.6 10.8c1.4 2.8 3.8 5.1 6.6 6.6l2.2-2.2c.3-.3.7-.4 1-.2 1.1.4 2.3.6 3.6.6.6 0 1 .4 1 1V20c0 .6-.4 1-1 1C10.6 21 3 13.4 3 4c0-.6.4-1 1-1h3.5c.6 0 1 .4 1 1 0 1.3.2 2.5.6 3.6.1.3 0 .7-.2 1L6.6 10.8z"/></svg>
        <span class="contacts__text" style="top:-1px">000 111 222 333</span>
      </li>
      <li class="contacts__item" style="top:276px">
        <svg class="contacts__icon" viewBox="0 0 24 24" aria-hidden="true"><path d="M10 20v-6h4v6h5v-8h3L12 3 2 12h3v8z"/></svg>
        <span class="contacts__text" style="top:-19px">Your Address<br>Street Location,City</span>
      </li>
      <li class="contacts__item" style="top:326px">
        <svg class="contacts__icon" viewBox="0 0 24 24" aria-hidden="true"><path d="M2 5h20v14H2V5zm2 2v.5l8 5.5 8-5.5V7l-8 5.5L4 7zm0 3v7h16v-7l-8 5.5L4 10z"/></svg>
        <span class="contacts__text" style="top:-3px">YourName@Mailbox.com</span>
      </li>
      <li class="contacts__item" style="top:372px">
        <svg class="contacts__icon" viewBox="0 0 24 24" aria-hidden="true"><path d="M12 2a10 10 0 1 0 0 20 10 10 0 0 0 0-20zm7.9 9h-3.4a15 15 0 0 0-1.4-6.2A8 8 0 0 1 19.9 11zM12 4c1 1.3 2.3 3.8 2.5 7h-5C9.7 7.8 11 5.3 12 4zM8.9 4.8A15 15 0 0 0 7.5 11H4.1a8 8 0 0 1 4.8-6.2zM4.1 13h3.4a15 15 0 0 0 1.4 6.2A8 8 0 0 1 4.1 13zM12 20c-1-1.3-2.3-3.8-2.5-7h5c-.2 3.2-1.5 5.7-2.5 7zm3.1-.8a15 15 0 0 0 1.4-6.2h3.4a8 8 0 0 1-4.8 6.2z"/></svg>
        <span class="contacts__text" style="top:-2px">www.YourCompany.com</span>
      </li>
    </ul>
  </section>

  <section class="card card--back" aria-label="Business card back">
    <p class="brand brand--back">Blue Heron Journeys</p>
  </section>
</main>
</body>
</html>
```